Unternehmen für Ordnung und Sauberkeit am Arbeitsplatz und Produkte zur Produktionsoptimierung benötigt Visitenkarten und Briefpapier
Zielgruppe
Produkte für Ordnung und Sauberkeit am Arbeitsplatz, Organisation von Arbeitsplätzen, Produkte zur Vereinfachung von Arbeitsabläufen, Produkte zur Produktionsoptimierung unter dem Lean Gedanke, Schlagwort: "5S", nachhaltig, sauber
Aufgabenstellung
Wir sind auf der Suche nach Visitenkarten und Briefpapier für das Unternehmen yourTidor. Nachhaltig, Sauber usw.. Unser Firmenlogo finden Sie anbei.

```html
<!DOCTYPE html>
<html lang="de">
<head>
<meta charset="utf-8">
<title>yourTidor – Briefpapier und Kuvert</title>
<link rel="stylesheet" href="https://fonts.googleapis.com/css2?family=Source+Sans+3:wght@400;700&family=Roboto:wght@400&display=swap">
<style>
  :root {
    --green: #1d6a31;
    --green-bright: #23922f;
    --panel-grey: #4a4a4a;
    --strip-grey: #8c8c8c;
    --text-grey: #9a9a9a;
    --paper: #ffffff;
    --mark: #333333;
    --ghost: #f4f4f4;
  }
  * { margin: 0; padding: 0; box-sizing: border-box; }
  html, body { width: 1200px; height: 1000px; overflow: hidden; background: #fff; }
  body { position: relative; font-family: "Source Sans 3", sans-serif; }

  .crop-marks { position: absolute; inset: 0; }

  /* Letterhead */
  .letterhead {
    position: absolute; left: 96px; top: 203px; width: 420px; height: 594px;
    background: var(--paper); box-shadow: 2px 2px 4px rgba(0,0,0,.35); overflow: hidden;
  }
  .letterhead__header { position: absolute; left: 0; top: 0; width: 100%; height: 103px; background: var(--green); }
  .letterhead__brand {
    position: absolute; left: 0; top: 0; width: 299px; height: 103px;
    display: flex; align-items: center; justify-content: center; gap: 8px;
    color: #fff; font-weight: 700; font-size: 30px;
  }
  .brand-dot { width: 18px; height: 18px; border-radius: 50%; background: #fff; display: inline-block; }
  .letterhead__contact {
    position: absolute; right: 0; top: 0; width: 121px; height: 103px; background: var(--panel-grey);
    color: #e6e6e6; font-size: 6.4px; line-height: 1.25; padding: 16px 0 0 9px;
  }
  .contact-row { display: flex; align-items: flex-start; gap: 7px; margin-bottom: 4px; }
  .contact-row svg { flex: none; width: 10px; height: 10px; }
  .contact-name { color: #fff; font-weight: 700; font-size: 8px; }
  .letterhead__ghost {
    position: absolute; left: 60px; top: 310px; font-size: 74px; font-weight: 700; color: var(--ghost);
  }
  .letterhead__footer {
    position: absolute; left: 0; bottom: 0; width: 100%; height: 47px; background: var(--green);
    display: flex; align-items: center; color: #fff; font-size: 6px; line-height: 1.4;
  }
  .footer-brand { width: 136px; text-align: center; font-weight: 700; font-size: 13px; }
  .footer-divider { width: 1px; height: 23px; background: #fff; }
  .footer-bank { width: 132px; padding-left: 37px; }
  .footer-iban { padding-left: 41px; }

  /* Envelopes */
  .envelope { position: absolute; left: 653px; width: 450px; }
  .envelope__body { position: absolute; left: 0; width: 450px; background: var(--paper); box-shadow: 2px 2px 4px rgba(0,0,0,.35); overflow: hidden; }
  .envelope--front { top: 183px; height: 302px; }
  .envelope--front .envelope__body { top: 71px; height: 231px; }
  .envelope__flap { position: absolute; left: 0; width: 450px; height: 72px; }
  .flap-label { position: absolute; left: 0; width: 450px; text-align: center; color: #fff; font-weight: 700; font-size: 17px; }
  .flap-label--inverted { top: 20px; transform: rotate(180deg); }
  .sender { position: absolute; left: 27px; top: 24px; font-size: 6.2px; color: var(--text-grey); line-height: 1.45; padding-left: 14px; }
  .sender svg { position: absolute; left: 0; top: 1px; width: 10px; height: 11px; }
  .sender__name { color: var(--green-bright); font-weight: 700; font-size: 9.5px; line-height: 1.1; }
  .address-window {
    position: absolute; left: 27px; top: 130px; width: 181px; height: 72px;
    border: 1px solid #cfcfcf; border-radius: 8px; box-shadow: inset 1px 1px 4px rgba(0,0,0,.25);
    font-family: "Roboto", sans-serif; font-size: 6.2px; color: #555; line-height: 1.55; padding: 16px 0 0 35px;
  }
  .envelope__brand {
    position: absolute; right: 36px; top: 145px; display: flex; align-items: center; gap: 8px;
    color: var(--green); font-weight: 700; font-size: 30px;
  }
  .envelope__brand .brand-dot { background: var(--green); }
  .envelope__strip { position: absolute; left: 0; bottom: 0; width: 100%; height: 8px; }

  .envelope--back { top: 565px; height: 231px; }
  .envelope--back .envelope__body { top: 0; height: 231px; }
  .envelope--back .flap-label { top: 20px; }
</style>
</head>
<body>

<svg class="crop-marks" width="1200" height="1000" aria-hidden="true">
  <g stroke="var(--mark)" stroke-width="0.6" fill="none">
    <line x1="96" y1="165" x2="96" y2="190"/><line x1="516" y1="165" x2="516" y2="190"/>
    <line x1="58" y1="203" x2="83" y2="203"/><line x1="529" y1="203" x2="554" y2="203"/>
    <line x1="58" y1="797" x2="83" y2="797"/><line x1="529" y1="797" x2="554" y2="797"/>
    <line x1="96" y1="810" x2="96" y2="835"/><line x1="516" y1="810" x2="516" y2="835"/>
    <line x1="88" y1="406" x2="109" y2="406"/><line x1="88" y1="595" x2="109" y2="595"/>

    <line x1="653" y1="216" x2="653" y2="241"/><line x1="1103" y1="216" x2="1103" y2="241"/>
    <line x1="615" y1="254" x2="640" y2="254" stroke-dasharray="4 4"/><line x1="1116" y1="254" x2="1141" y2="254" stroke-dasharray="4 4"/>
    <line x1="615" y1="485" x2="640" y2="485"/><line x1="1116" y1="485" x2="1141" y2="485"/>
    <line x1="653" y1="497" x2="653" y2="522"/><line x1="1103" y1="497" x2="1103" y2="522"/>
    <line x1="653" y1="528" x2="653" y2="553"/><line x1="1103" y1="528" x2="1103" y2="553"/>
    <line x1="615" y1="566" x2="640" y2="566" stroke-dasharray="4 4"/><line x1="1116" y1="566" x2="1141" y2="566" stroke-dasharray="4 4"/>
    <line x1="615" y1="796" x2="640" y2="796"/><line x1="1116" y1="796" x2="1141" y2="796"/>
    <line x1="653" y1="809" x2="653" y2="834"/><line x1="1103" y1="809" x2="1103" y2="834"/>
  </g>
</svg>

<section class="letterhead" aria-label="Briefpapier">
  <header class="letterhead__header">
    <div class="letterhead__brand"><span class="brand-dot"></span>yourTidor</div>
    <div class="letterhead__contact">
      <div class="contact-row">
        <svg viewBox="0 0 10 10"><rect width="10" height="10" rx="2" fill="#fff" opacity=".85"/><path d="M5 2a2 2 0 0 0-2 2c0 1.5 2 4 2 4s2-2.5 2-4a2 2 0 0 0-2-2z" fill="var(--green)"/></svg>
        <div><div class="contact-name">yourTidor</div>Lindenweg 12<br>95100 Talheim</div>
      </div>
      <div class="contact-row">
        <svg viewBox="0 0 10 10"><rect width="10" height="10" rx="2" fill="#fff" opacity=".85"/><path d="M2 4c0-1 1-1.5 3-1.5S8 3 8 4v1H2zM3 5h4l.5 2.5h-5z" fill="var(--green)"/></svg>
        <div>04210 / 55310 2</div>
      </div>
      <div class="contact-row">
        <svg viewBox="0 0 10 10"><rect width="10" height="10" rx="2" fill="#fff" opacity=".85"/><rect x="2.5" y="2" width="5" height="6" fill="none" stroke="var(--green)" stroke-width=".8"/></svg>
        <div>04210 / 55310 / 3 7</div>
      </div>
      <div class="contact-row">
        <svg viewBox="0 0 10 10"><rect width="10" height="10" rx="2" fill="#fff" opacity=".85"/><text x="5" y="7.5" font-size="7" text-anchor="middle" fill="var(--green)" font-family="sans-serif">@</text></svg>
        <div>info@yourtidor.de</div>
      </div>
      <div class="contact-row">
        <svg viewBox="0 0 10 10"><rect width="10" height="10" rx="2" fill="#fff" opacity=".85"/><circle cx="5" cy="5" r="2.8" fill="none" stroke="var(--green)" stroke-width=".8"/><line x1="2.2" y1="5" x2="7.8" y2="5" stroke="var(--green)" stroke-width=".6"/></svg>
        <div>www.yourtidor-shop.de</div>
      </div>
    </div>
  </header>
  <div class="letterhead__ghost" aria-hidden="true">yourTidor</div>
  <footer class="letterhead__footer">
    <div class="footer-brand">yourTidor</div>
    <span class="footer-divider"></span>
    <div class="footer-bank">Sparkasse Talgrund<br>BLZ 000 400 00<br>Kto 100000000</div>
    <span class="footer-divider"></span>
    <div class="footer-iban">IBAN: DE12300400000012345678<br>BIC: TALGDE2TXXX</div>
  </footer>
</section>

<section class="envelope envelope--front" aria-label="Kuvert Vorderseite">
  <svg class="envelope__flap" style="top:0" viewBox="0 0 450 72" aria-hidden="true">
    <path d="M0 72 L22 8 Q25 0 34 0 H416 Q425 0 428 8 L450 72 Z" fill="var(--green)"/>
  </svg>
  <div class="flap-label flap-label--inverted">yourTidor</div>
  <div class="envelope__body">
    <div class="sender">
      <svg viewBox="0 0 10 11"><path d="M5 .5a4 4 0 0 0-4 4c0 3 4 6 4 6s4-3 4-6a4 4 0 0 0-4-4z" fill="#666"/><circle cx="5" cy="4.5" r="1.5" fill="#fff"/></svg>
      <div class="sender__name">yourTidor</div>
      Lindenweg 12<br>95100 Talheim
    </div>
    <div class="address-window">Marlene Weber<br>Am Birkenhang 8<br>53700 Waldstetten<br>SCHWEIZ</div>
    <div class="envelope__brand"><span class="brand-dot"></span>yourTidor</div>
    <svg class="envelope__strip" viewBox="0 0 450 8" preserveAspectRatio="none" aria-hidden="true">
      <polygon points="0,0 296,0 290,8 0,8" fill="var(--strip-grey)"/>
      <polygon points="304,0 450,0 450,8 298,8" fill="var(--green)"/>
    </svg>
  </div>
</section>

<section class="envelope envelope--back" aria-label="Kuvert Rückseite">
  <div class="envelope__body"></div>
  <svg class="envelope__flap" style="top:0" viewBox="0 0 450 72" aria-hidden="true">
    <path d="M0 0 H450 L428 64 Q425 72 416 72 H34 Q25 72 22 64 Z" fill="var(--green)"/>
  </svg>
  <div class="flap-label">yourTidor</div>
</section>

</body>
</html>
```